Business Card Design

Looking for business card designs for a new business. there will be two cards of the same design (both lots of information below in contact info). We would like the logo diagonally across the card with the information split above and below the logo similar to sketch. happy to look at similar alternatives
Please use same colours as in logo design

Industry/Entity Type

Business

Contact Information for Business Card

Dwight Halloran
mob - 0491 738 204
ph - 02 6148 3920
fax - 02 6148 3975
email - dwight@kestrelbeams.com.au
14 Larkmoor Road, Taminda NSW 2340

Colin Marchetti
mob - 0438 912 557
ph - 02 6148 3920
fax - 02 6148 3975
email - colin@kestrelbeams.com.au

```html
<!DOCTYPE html>
<html lang="en">
<head>
<meta charset="utf-8">
<title>Kestrel Beams – Business Cards</title>
<link href="https://fonts.googleapis.com/css2?family=Open+Sans:wght@400;700&display=swap" rel="stylesheet">
<style>
  :root {
    --teal: #167d77;
    --ink: #111111;
    --text: #222222;
    --card: #ffffff;
    --backdrop: #8c4b26;
    --edge: #3a2416;
  }
  * { box-sizing: border-box; margin: 0; padding: 0; }
  html, body {
    width: 768px;
    height: 1200px;
    overflow: hidden;
  }
  body {
    background: var(--backdrop);
    font-family: "Open Sans", Arial, sans-serif;
    position: relative;
  }
  .card {
    position: absolute;
    background: var(--card);
    border: 1px solid var(--edge);
    overflow: hidden;
  }
  .card--front { left: 30px; top: 28px; width: 714px; height: 410px; }
  .card--back  { left: 192px; top: 464px; width: 407px; height: 714px; }

  .card__rules { position: absolute; inset: 0; width: 100%; height: 100%; }
  .card__rules line { stroke: var(--teal); stroke-width: 2.5; }

  .holder-name {
    position: absolute;
    left: 12px;
    top: 12px;
    font-size: 21px;
    font-weight: 700;
    color: var(--teal);
  }

  .wordmark {
    position: absolute;
    display: flex;
    align-items: center;
    gap: 12px;
    white-space: nowrap;
    font-weight: 700;
    color: var(--ink);
    line-height: 1;
  }
  .wordmark__square { background: var(--teal); flex: none; }
  .card--front .wordmark {
    left: 262px; top: 162px;
    font-size: 46px;
    transform: translate(-50%, -50%) rotate(-24deg);
  }
  .card--front .wordmark__square { width: 30px; height: 30px; }
  .card--back .wordmark {
    left: 214px; top: 357px;
    font-size: 60px;
    transform: translate(-50%, -50%) rotate(90deg);
  }
  .card--back .wordmark__square { width: 40px; height: 40px; }

  .contact-list {
    position: absolute;
    right: 18px;
    top: 234px;
    list-style: none;
    text-align: right;
    font-size: 17px;
    color: var(--text);
    line-height: 27px;
  }
  .contact-list li { display: flex; justify-content: flex-end; align-items: center; gap: 5px; }
  .contact-list svg { width: 14px; height: 14px; fill: var(--text); flex: none; }
  .address {
    position: absolute;
    right: 18px;
    top: 366px;
    font-size: 17px;
    color: var(--text);
  }

  .website {
    position: absolute;
    left: 67px;
    top: 339px;
    font-size: 20px;
    letter-spacing: 3px;
    color: var(--text);
    white-space: nowrap;
    transform: translate(-50%, -50%) rotate(90deg);
  }
</style>
</head>
<body>

<section class="card card--front" aria-label="Business card front">
  <svg class="card__rules" viewBox="0 0 714 410" preserveAspectRatio="none" aria-hidden="true">
    <line x1="0" y1="199" x2="700" y2="0"/>
    <line x1="0" y1="404" x2="714" y2="49"/>
  </svg>

  <h1 class="holder-name">Colin Marchetti</h1>

  <div class="wordmark">
    <span class="wordmark__square"></span>
    <span class="wordmark__name">Kestrel Beams</span>
  </div>

  <ul class="contact-list">
    <li>
      <svg viewBox="0 0 16 16" aria-label="Phone"><path d="M3.5 1 6 4 4.6 5.6a9 9 0 0 0 5.8 5.8L12 10l3 2.5-1.6 2.3C7.5 15 1 8.5 1.2 2.6z"/></svg>
      02 6148 3920
    </li>
    <li>
      <svg viewBox="0 0 16 16" aria-label="Mobile"><path d="M5 1h6a1 1 0 0 1 1 1v12a1 1 0 0 1-1 1H5a1 1 0 0 1-1-1V2a1 1 0 0 1 1-1zm0 2v8h6V3zm3 9.2a.9.9 0 1 0 0 1.8.9.9 0 0 0 0-1.8z"/></svg>
      0438 912 557
    </li>
    <li>
      <svg viewBox="0 0 16 16" aria-label="Fax"><path d="M4 1h7v4H4zM2 6h12a1 1 0 0 1 1 1v6h-3v2H4v-2H1V7a1 1 0 0 1 1-1zm3 5v3h6v-3z"/></svg>
      02 6148 3975
    </li>
    <li>
      <svg viewBox="0 0 16 16" aria-label="Email"><path d="M1 4h14v9H1zm1.2 1 5.8 4.2L13.8 5z"/></svg>
      colin@kestrelbeams.com.au
    </li>
  </ul>

  <p class="address">14 Larkmoor Road, Corbin Flats NSW 2352</p>
</section>

<section class="card card--back" aria-label="Business card back">
  <p class="website">www.kestrelbeams.com.au</p>
  <div class="wordmark">
    <span class="wordmark__square"></span>
    <span class="wordmark__name">Kestrel Beams</span>
  </div>
</section>

</body>
</html>
```